Business card for law firm

Need business card for new law firm. Think confident, authoritative, conservative, but not stuffy or old-fashioned.

Contact Information for Business Card

Content for card - logo (uploaded), plus the following:

Paul Whitcombe (larger font)
Managing Partner (larger font, but not as large as name)
Level 9, 7 Ferris Lane
Sydney NSW 2000
Main Tel 02 9364 2710
Direct Tel 02 8472 3159
Email paul@qvlegal.com.au
www.qvlegal.com.au

Letterhead design should include logo plus:
Level 9, 7 Ferris Lane
Sydney NSW 2000
Tel 02 8472 3159
www.qvlegal.com.au

```html
<!DOCTYPE html>
<html lang="en">
<head>
<meta charset="utf-8">
<title>Quayvale Legal – Business Card</title>
<link rel="stylesheet" href="https://fonts.googleapis.com/css2?family=Open+Sans:wght@400;600;700&display=swap">
<style>
  :root {
    --navy: #0d1d54;
    --ink: #1a1a1a;
    --white: #ffffff;
    --black: #050505;
    --bg-light: #eeeff0;
    --bg-dark: #c9cacc;
    --edge: #b9babd;
  }
  * { box-sizing: border-box; margin: 0; padding: 0; }
  html, body { width: 1200px; height: 1080px; overflow: hidden; }
  body {
    position: relative;
    background: radial-gradient(ellipse at 30% 20%, var(--bg-light) 0%, var(--bg-dark) 100%);
    font-family: "Open Sans", Arial, sans-serif;
  }
  .card {
    position: absolute;
    width: 781px;
    height: 445px;
    border-radius: 32px;
    overflow: hidden;
    box-shadow: 0 2px 6px rgba(0,0,0,0.18);
  }
  .card--front { left: 63px; top: 66px; background: var(--white); border: 1px solid var(--edge); }
  .card--back { left: 344px; top: 557px; background: var(--black); }

  .wave { position: absolute; left: 0; top: 0; width: 781px; height: 445px; }

  .brand { position: absolute; text-align: center; font-weight: 400; }
  .brand__mark { display: block; margin: 0 auto; width: 78px; height: 90px; }
  .brand__name { display: block; letter-spacing: 2px; line-height: 1; }
  .brand__sub { display: block; line-height: 1; }

  .card--front .brand { left: 40px; top: 64px; width: 370px; color: var(--ink); }
  .card--front .brand__mark { background: var(--navy); }
  .card--front .brand__name { margin-top: 48px; font-size: 44px; }
  .card--front .brand__sub { margin-top: 12px; font-size: 18px; letter-spacing: 16px; padding-left: 16px; }

  .person { position: absolute; left: 485px; top: 50px; color: var(--navy); }
  .person__name { font-size: 24px; font-weight: 700; text-transform: uppercase; letter-spacing: 0.3px; }
  .person__title { margin-top: 6px; font-size: 18px; color: #333; text-transform: uppercase; letter-spacing: 0.5px; }

  .contact { list-style: none; margin-top: 20px; }
  .contact__item { display: flex; align-items: center; height: 33.5px; font-size: 18.5px; color: var(--ink); }
  .contact__icon { width: 16px; height: 16px; margin-right: 8px; fill: var(--navy); flex: none; }

  .address {
    position: absolute; right: 52px; top: 352px;
    text-align: right; color: var(--white); font-size: 19px; line-height: 30px;
  }

  .card--back .brand { left: 0; top: 77px; width: 781px; color: var(--white); }
  .card--back .brand__mark { width: 86px; height: 110px; background: var(--white); }
  .card--back .brand__name { margin-top: 56px; font-size: 52px; letter-spacing: 3px; }
  .card--back .brand__sub { margin-top: 16px; font-size: 21px; letter-spacing: 20px; padding-left: 20px; }

  .web {
    position: absolute; left: 0; top: 376px; width: 781px;
    text-align: center; color: var(--white); font-size: 22px; letter-spacing: 4px;
  }
  .web strong { font-weight: 700; }
</style>
</head>
<body>

<section class="card card--front" aria-label="Business card front">
  <svg class="wave" viewBox="0 0 781 445" aria-hidden="true">
    <path fill="var(--navy)" d="M0,282 C25,360 95,398 200,398 C380,398 560,320 781,322 V445 H0 Z"/>
    <path fill="var(--white)" d="M42,388 C120,440 270,432 430,382 C570,338 690,300 771,298 C690,300 570,325 430,364 C280,408 135,425 42,388 Z"/>
    <path fill="var(--navy)" d="M330,388 C470,330 620,262 771,292 C640,278 500,320 330,388 Z"/>
  </svg>

  <div class="brand">
    <span class="brand__mark" aria-hidden="true"></span>
    <span class="brand__name">QUAYVALE</span>
    <span class="brand__sub">LEGAL</span>
  </div>

  <div class="person">
    <h1 class="person__name">Paul Whitcombe</h1>
    <p class="person__title">Managing Partner</p>
    <ul class="contact">
      <li class="contact__item">
        <svg class="contact__icon" viewBox="0 0 16 16" aria-hidden="true"><path d="M4 1 L6.5 4.5 L5 6.5 C6 8.5 7.5 10 9.5 11 L11.5 9.5 L15 12 L13 15 C7 14.5 1.5 9 1 3 Z"/></svg>
        02 9364 2710(Main)
      </li>
      <li class="contact__item">
        <svg class="contact__icon" viewBox="0 0 16 16" aria-hidden="true"><path d="M4 1 L6.5 4.5 L5 6.5 C6 8.5 7.5 10 9.5 11 L11.5 9.5 L15 12 L13 15 C7 14.5 1.5 9 1 3 Z"/></svg>
        02 8472 3159(Direct)
      </li>
      <li class="contact__item">
        <svg class="contact__icon" viewBox="0 0 16 16" aria-hidden="true"><path d="M1 6 L8 1.5 L15 6 V14 H1 Z M2.5 7 L8 11 L13.5 7 L8 3.5 Z" fill-rule="evenodd"/></svg>
        paul@qvlegal.com.au
      </li>
      <li class="contact__item">
        <svg class="contact__icon" viewBox="0 0 16 16" aria-hidden="true"><g fill="none" stroke="var(--navy)" stroke-width="1.3"><circle cx="8" cy="8" r="6.5"/><ellipse cx="8" cy="8" rx="3" ry="6.5"/><path d="M1.5 8 H14.5 M2.5 4.7 H13.5 M2.5 11.3 H13.5"/></g></svg>
        www.qvlegal.com.au
      </li>
    </ul>
  </div>

  <address class="address" style="font-style: normal;">
    Level 9, 7 Ferris Lane<br>
    Sydney NSW 2000
  </address>
</section>

<section class="card card--back" aria-label="Business card back">
  <div class="brand">
    <span class="brand__mark" aria-hidden="true"></span>
    <span class="brand__name">QUAYVALE</span>
    <span class="brand__sub">LEGAL</span>
  </div>
  <p class="web">www.<strong>qvlegal</strong>.com.au</p>
</section>

</body>
</html>
```